design a construction company business card

Design business card around our logo. Card must have all the typical info: name, title, address, phone, email, business name, etc. Somewhere on the card I would like to see our motto "Founded on trust... Driven by craftsmanship." Consider adding a splash of bright orange to the card to complement the blues and silvers/grays in the logo. We are open to metallic inks, textures, etc. We would like to see options on both light and dark backgrounds. The font in the logo is Euro Technic Extended Regular.

```html
<!DOCTYPE html>
<html lang="en">
<head>
<meta charset="utf-8">
<title>Halden Contracting — Business Card</title>
<link href="https://fonts.googleapis.com/css2?family=Michroma&family=Lato:wght@400&family=Roboto:wght@400&display=swap" rel="stylesheet">
<style>
  :root {
    --backdrop: #2e2e2f;
    --card-white: #ffffff;
    --brand-blue: #1f4aa8;
    --blue-top: #1a6dbb;
    --blue-bottom: #2249a3;
    --steel-gray: #6d6e70;
    --text-gray: #505052;
    --rule-gray: #d9d9d9;
    --line-gray: #8a8a8a;
  }
  * { margin: 0; padding: 0; box-sizing: border-box; }
  html, body { width: 1200px; height: 1200px; overflow: hidden; }
  body { background: var(--backdrop); position: relative; font-family: "Lato", sans-serif; }

  .card {
    position: absolute;
    top: 310px;
    height: 594px;
    box-shadow: 0 4px 10px rgba(0,0,0,0.45);
    overflow: hidden;
  }
  .card-front { left: 234px; width: 364px; background: var(--card-white); text-align: center; }
  .card-back  { left: 627px; width: 369px; background: var(--steel-gray); }

  /* front */
  .company {
    position: absolute; left: 0; right: 0; top: 165px;
    color: var(--brand-blue);
    font-family: "Michroma", sans-serif; font-weight: 400;
  }
  .company-name { font-size: 44px; line-height: 1; letter-spacing: 2px; }
  .company-suffix { font-size: 15px; margin-top: 14px; letter-spacing: 0.5px; }

  .person-name {
    position: absolute; left: 0; right: 0; top: 331px;
    font-family: "Michroma", sans-serif; font-size: 21px; font-weight: 400; line-height: 1;
    color: var(--brand-blue); letter-spacing: 0.5px;
  }
  .person-title {
    position: absolute; left: 0; right: 0; top: 360px;
    font-size: 17px; line-height: 20px; color: var(--text-gray);
  }
  .contact-icons { position: absolute; left: 87px; top: 394px; }

  .contact-list, .address {
    position: absolute; left: 0; right: 0;
    font-size: 17px; line-height: 22px; color: var(--text-gray); list-style: none;
  }
  .contact-list { top: 431px; }
  .divider {
    position: absolute; left: 88px; width: 196px; top: 506px;
    border-top: 1px solid var(--rule-gray);
  }
  .address { top: 517px; font-style: normal; }

  /* back */
  .back-field {
    position: absolute; left: 0; top: 0; width: 100%; height: 435px;
    background: linear-gradient(180deg, var(--blue-top) 0%, var(--blue-bottom) 100%);
  }
  .back-rule { position: absolute; left: 0; top: 435px; width: 100%; height: 4px; background: var(--card-white); }
  .motto {
    position: absolute; left: 0; right: 0; top: 511px;
    font-family: "Roboto", sans-serif; font-size: 19px; line-height: 25px;
    color: var(--card-white); text-align: center; text-transform: uppercase;
  }
</style>
</head>
<body>

<section class="card card-front">
  <div class="company">
    <div class="company-name">HALDEN</div>
    <div class="company-suffix">CONTRACTING, INC.</div>
  </div>

  <h1 class="person-name">MARCUS REYES</h1>
  <p class="person-title">Managing Director</p>

  <svg class="contact-icons" width="190" height="28" viewBox="0 0 190 28" aria-hidden="true">
    <line x1="0" y1="14" x2="52" y2="14" stroke="var(--line-gray)" stroke-width="1"/>
    <line x1="138" y1="14" x2="190" y2="14" stroke="var(--line-gray)" stroke-width="1"/>
    <circle cx="67" cy="14" r="12" fill="var(--brand-blue)"/>
    <path d="M60 12 q7 -6 14 0 l-2 2 h-2 l-1 -2 h-4 l-1 2 h-2 z M61 15 h12 v5 h-12 z" fill="#fff"/>
    <circle cx="95" cy="14" r="12" fill="var(--brand-blue)"/>
    <rect x="88" y="9" width="14" height="10" fill="#fff"/>
    <path d="M88 9 l7 6 l7 -6" fill="none" stroke="var(--brand-blue)" stroke-width="1.3"/>
    <circle cx="123" cy="14" r="12" fill="var(--brand-blue)"/>
    <circle cx="123" cy="14" r="7" fill="none" stroke="#fff" stroke-width="1.5"/>
    <ellipse cx="123" cy="14" rx="3" ry="7" fill="none" stroke="#fff" stroke-width="1.2"/>
    <line x1="116" y1="14" x2="130" y2="14" stroke="#fff" stroke-width="1.2"/>
  </svg>

  <ul class="contact-list">
    <li>044-555 019 274</li>
    <li>hello@haldenbuild.com</li>
    <li>www.haldenbuild.com</li>
  </ul>
  <div class="divider"></div>
  <address class="address">
    18, Foundry Lane,<br>45460,Westmark
  </address>
</section>

<section class="card card-back">
  <div class="back-field" role="img" aria-label="Large white company building mark on a blue gradient"></div>
  <div class="back-rule"></div>
  <p class="motto">Founded on trust... driven<br>by craftsmanship</p>
</section>

</body>
</html>
```